Moravel Aesthetic Doctor

I require an elegant, luxurious looking business card for my aesthetic business. I am a doctor and that will set me aside from competitors. I am planning to provide home and spa based treatments to clients with high expectations. I have attached my logo.

```html
<!DOCTYPE html>
<html lang="en">
<head>
<meta charset="utf-8">
<title>Moravel Aesthetic Doctor – Business Card</title>
<link rel="stylesheet" href="https://fonts.googleapis.com/css2?family=Roboto:wght@400;500&family=Saira+Semi+Condensed:wght@600&display=swap">
<style>
  :root {
    --backdrop: #b9b9b9;
    --card: #f1f2f3;
    --card-edge: #e3e4e6;
    --ink: #2b2b2b;
    --brand-grey: #6f7a8c;
    --brand-blue: #3f92cf;
    --band-deep: #1464a8;
    --band-light: #4a9ad3;
    --strip-grey: #b4b7bb;
    --motif: #e2e3e5;
  }
  * { box-sizing: border-box; margin: 0; padding: 0; }
  html, body { width: 1200px; height: 576px; overflow: hidden; }
  body {
    background: var(--backdrop);
    font-family: "Roboto", Arial, sans-serif;
    color: var(--ink);
    position: relative;
  }
  .card {
    position: absolute;
    top: 138px;
    width: 484px;
    height: 294px;
    border-radius: 10px;
    background: linear-gradient(180deg, #f6f7f8 0%, var(--card) 60%, var(--card-edge) 100%);
    box-shadow: 0 3px 6px rgba(0,0,0,.25);
    overflow: hidden;
  }
  .card--front { left: 82px; }
  .card--back { left: 602px; width: 481px; height: 292px; }

  /* brand lockup */
  .brand { position: absolute; display: flex; align-items: center; }
  .brand__dot {
    border: 2px solid var(--brand-grey);
    border-radius: 50%;
    flex: none;
  }
  .brand__name {
    font-family: "Roboto", Arial, sans-serif;
    font-weight: 400;
    color: var(--brand-grey);
    text-transform: uppercase;
    line-height: 1;
  }
  .brand__name span { display: block; }
  .card--front .brand { left: 94px; top: 62px; gap: 18px; }
  .card--front .brand__dot { width: 80px; height: 80px; }
  .card--front .brand__name .main { font-size: 44px; letter-spacing: 2px; }
  .card--front .brand__name .sub { font-size: 19px; letter-spacing: 1.5px; margin-top: 8px; }

  .card--back .brand { left: 26px; top: 32px; gap: 16px; }
  .card--back .brand__dot { width: 94px; height: 94px; }
  .card--back .brand__name .main { font-size: 44px; letter-spacing: 2px; }
  .card--back .brand__name .sub { font-size: 19px; letter-spacing: 1.5px; margin-top: 8px; }

  .services {
    position: absolute;
    left: 0; right: 0; top: 194px;
    text-align: center;
    font-size: 13.5px;
    line-height: 19px;
  }
  .services .sep { color: var(--brand-blue); margin: 0 8px; }

  .band {
    position: absolute;
    color: #fff;
    font-size: 13px;
    letter-spacing: .6px;
    text-transform: uppercase;
    display: flex; align-items: center; justify-content: center;
  }
  .card--front .band {
    left: 0; right: 0; top: 240px; height: 34px;
    background: linear-gradient(90deg, var(--band-deep) 0%, var(--band-light) 50%, var(--band-deep) 100%);
  }

  .motif {
    position: absolute;
    right: 0; top: 10px;
    width: 190px; height: 240px;
    background: radial-gradient(ellipse at 60% 50%, var(--motif) 0%, rgba(226,227,229,0) 70%);
  }

  .doctor { position: absolute; left: 24px; top: 163px; }
  .doctor__name {
    font-family: "Saira Semi Condensed", Arial, sans-serif;
    font-weight: 600;
    font-size: 18px;
    color: #333;
  }
  .doctor__post { font-family: "Roboto", Arial, sans-serif; font-weight: 400; font-size: 10px; color: var(--brand-blue); margin-left: 4px; }
  .doctor__qual { font-size: 13px; line-height: 16px; color: var(--brand-blue); margin-top: 4px; }

  .contact { position: absolute; left: 243px; top: 165px; list-style: none; font-size: 13px; }
  .contact li { display: flex; align-items: center; height: 18.5px; }
  .contact svg { width: 10px; height: 10px; margin-right: 10px; fill: var(--brand-grey); }

  .social { position: absolute; left: 24px; top: 247px; font-size: 12.5px; display: flex; align-items: center; gap: 4px; }
  .social .dot { width: 12px; height: 12px; border-radius: 50%; background: var(--brand-blue); }
  .social .dot:first-of-type { margin-left: 4px; }

  .strip { position: absolute; left: 0; right: 0; bottom: 0; height: 8px; background: var(--strip-grey); }
  .card--back .band { left: 0; right: 0; top: 256px; bottom: 0; }
  .card--back .band svg { position: absolute; inset: 0; width: 100%; height: 100%; }
  .card--back .band .band__text { position: relative; margin-left: 190px; }
</style>
</head>
<body>

  <section class="card card--front" aria-label="Card front">
    <div class="brand">
      <span class="brand__dot"></span>
      <div class="brand__name"><span class="main">Moravel</span><span class="sub">Aesthetic Doctor</span></div>
    </div>
    <div class="services">
      <p>Dermal Injectables<span class="sep">|</span>Plasma Facials<span class="sep">|</span>Microneedling</p>
      <p>Skin Boosters<span class="sep">|</span>Excessive Sweating</p>
    </div>
    <div class="band">Home and Spa Based Treatments</div>
  </section>

  <section class="card card--back" aria-label="Card back">
    <div class="motif" role="img" aria-label="Faint decorative brand motif"></div>
    <div class="brand">
      <span class="brand__dot"></span>
      <div class="brand__name"><span class="main">Moravel</span><span class="sub">Aesthetic Doctor</span></div>
    </div>

    <div class="doctor">
      <p class="doctor__name">Dr Elise Varden<span class="doctor__post">MRCPCH MD</span></p>
      <p class="doctor__qual">Australasian Diploma<br>of Aesthetic Medicine</p>
    </div>

    <ul class="contact">
      <li><svg viewBox="0 0 10 10"><path d="M2 0.5 L3.6 2.6 L2.7 3.7 Q3.8 5.9 6.3 7.3 L7.4 6.4 L9.5 8 L8.3 9.5 Q4.5 9.3 1.6 6.1 Q0.2 4.2 0.5 1.7 Z"/></svg>0800 555 018</li>
      <li><svg viewBox="0 0 10 10"><path d="M0.5 2 H9.5 V8 H0.5 Z M0.8 2.2 L5 5.4 L9.2 2.2" stroke="#f1f2f3" stroke-width=".8"/></svg>elise@moravel.co.nz</li>
      <li><svg viewBox="0 0 10 10"><circle cx="5" cy="5" r="4.3" fill="none" stroke="#6f7a8c" stroke-width="1"/><path d="M0.7 5 H9.3 M5 0.7 Q2.6 5 5 9.3 M5 0.7 Q7.4 5 5 9.3" fill="none" stroke="#6f7a8c" stroke-width=".8"/></svg>www.moravel.co.nz</li>
    </ul>

    <div class="social">Follow us on:<span class="dot"></span><span class="dot"></span></div>

    <div class="strip"></div>
    <div class="band">
      <svg viewBox="0 0 481 36" preserveAspectRatio="none" aria-hidden="true">
        <defs>
          <linearGradient id="bandFill" x1="0" x2="1">
            <stop offset="0" stop-color="#1464a8"/>
            <stop offset=".5" stop-color="#4a9ad3"/>
            <stop offset="1" stop-color="#1464a8"/>
          </linearGradient>
        </defs>
        <path d="M212 36 L228 4 Q230 0 236 0 H481 V36 Z" fill="url(#bandFill)"/>
      </svg>
      <span class="band__text">Home and Spa Based Treatments</span>
    </div>
  </section>

</body>
</html>
```